Brightvale cleaning and maintenance company

An expansive website whereby we can advertise our commercial cleaning and maintenance services across a service portfolio of commercial cleaning and property maintenance. Whereby potential skilled resources can deposit there resume so we can collaborate and match candidates to a broad range of cleaning and maintenance jobs/projects.
Updates

Looking for more extensive ideas so the front page can change pictures on it with the focus for Brightvale Commercial Cleaning and Maintenance. Also need to bring in all the portfolios we offer including 1. Equipment Cleaning and Sanitisation Services 2. High pressure gurney and play ground equipment cleaning 3. General Cleaning and Property Facilities Management 4. Project and Recruiting Services, to allow for potential professional cleaners, handy man, mechanics, warehousing resources , electricians to deposit there resume. Most of the designers have stuck with the old portfolio categories , however the portfolio of services we offer has been updated so that needs to be reflected in the website. Also not necessary to use all my original photos I would like the opening page of the website to perhaps be able to change and have different pictures is that possible thank you

```html
<!DOCTYPE html>
<html lang="en">
<head>
<meta charset="utf-8">
<title>Brightvale — Commercial Cleaning &amp; Maintenance</title>
<link href="https://fonts.googleapis.com/css2?family=Lato:wght@300;400;700;900&family=Montserrat:wght@500;600;800&family=Merriweather:wght@400;700&display=swap" rel="stylesheet">
<style>
:root{
  --navy:#0d3f86;
  --orange:#ff5a0f;
  --ink:#1e1e1e;
  --muted:#777;
  --soft:#f3f3f3;
  --footer:#2e2e2e;
  --white:#fff;
}
*{margin:0;padding:0;box-sizing:border-box}
html,body{width:1200px;height:3946px;overflow:hidden}
body{position:relative;background:var(--white);font-family:"Lato",sans-serif;color:var(--ink)}
.abs{position:absolute}

/* header */
.site-header{left:0;top:0;width:1200px;height:89px;background:var(--white)}
.brand{top:18px;display:flex;align-items:center;gap:10px;font-family:"Merriweather",serif;font-size:30px;color:var(--navy)}
.brand-dot{width:34px;height:34px;border-radius:50%;background:var(--navy)}
.main-nav a{color:var(--ink);text-decoration:none;position:absolute;white-space:nowrap;font-size:14px;font-weight:700;text-transform:uppercase}
.main-nav a.active{color:var(--orange)}

/* hero */
.hero{left:0;top:89px;width:1200px;height:564px;
  background:
    radial-gradient(ellipse 220px 160px at 1010px 470px,rgba(40,110,190,.85),rgba(40,110,190,0)),
    radial-gradient(ellipse 120px 90px at 930px 400px,rgba(240,210,40,.85),rgba(240,210,40,0)),
    radial-gradient(ellipse 200px 260px at 910px 260px,rgba(245,246,248,.95),rgba(245,246,248,0)),
    radial-gradient(ellipse 380px 140px at 420px 520px,rgba(230,232,233,.9),rgba(230,232,233,0)),
    linear-gradient(90deg,#4d5053 0%,#7c8084 25%,#aeb2b5 50%,#5a5f63 75%,#3c4044 100%)}
.hero-title{left:107px;top:170px;font-family:"Montserrat",sans-serif;font-size:52px;line-height:60px;color:var(--white);text-shadow:0 2px 6px rgba(0,0,0,.3)}
.hero-title .light{font-weight:500}
.hero-title .strong{font-weight:800;text-transform:uppercase}
.btn{display:flex;align-items:center;justify-content:center;gap:8px;background:var(--navy);color:var(--white);font-size:14px;font-weight:700;text-transform:uppercase;border-radius:2px;text-decoration:none}
.hero-btn{left:107px;top:510px;width:151px;height:51px}
.slider-arrow{top:348px;width:42px;height:42px;border-radius:50%;background:var(--white);display:flex;align-items:center;justify-content:center}
.scroll-cue{left:588px;top:580px}

/* feature band */
.feature-band{left:0;top:653px;width:1200px;height:157px;background:var(--navy)}
.feature{color:var(--white)}
.feature h4{font-size:14px;font-weight:700;text-transform:uppercase;margin-bottom:8px}
.feature .bar{width:28px;height:2px;background:var(--white);margin-bottom:9px}
.feature p{font-size:14px;line-height:21px}
.feature-divider{top:689px;width:1px;height:88px;background:rgba(255,255,255,.6)}

/* section heading */
.section-title{display:flex;align-items:center;gap:14px;font-family:"Merriweather",serif;font-size:35px;font-weight:700;color:var(--ink);text-transform:uppercase;white-space:nowrap}
.section-title .accent{color:var(--orange);font-weight:400}
.title-dot{width:24px;height:24px;border-radius:50%;background:var(--navy)}

/* services */
.service-card{width:479px;height:372px}
.service-photo{width:100%;height:302px}
.service-label{height:70px;background:var(--orange);color:var(--white);text-align:center;font-family:"Merriweather",serif;font-size:15px;line-height:21px;padding-top:14px;text-transform:uppercase}
.service-label b{font-weight:700;display:block}
.service-label span{font-weight:400}
.view-more{left:525px;top:1815px;width:150px;height:51px}

.water-band{left:0;top:1925px;width:1200px;height:85px;background:
  radial-gradient(ellipse 300px 30px at 200px 45px,rgba(160,195,225,.55),rgba(160,195,225,0)),
  radial-gradient(ellipse 340px 28px at 820px 40px,rgba(160,195,225,.55),rgba(160,195,225,0)),
  linear-gradient(180deg,rgba(255,255,255,0) 0%,#e4eef6 45%,#d3e3f0 55%,rgba(255,255,255,0) 100%)}

/* working with us */
.work-photo-a{left:111px;top:2068px;width:338px;height:339px;background:
  radial-gradient(ellipse 90px 140px at 270px 130px,rgba(70,80,90,.8),rgba(70,80,90,0)),
  radial-gradient(ellipse 60px 120px at 50px 240px,rgba(90,95,100,.9),rgba(90,95,100,0)),
  linear-gradient(135deg,#3f6a22,#5c8a32 45%,#2f4f1c 75%,#6a6f72)}
.work-photo-b{left:244px;top:2210px;width:303px;height:294px;background:
  radial-gradient(ellipse 140px 60px at 150px 200px,rgba(210,212,214,.9),rgba(210,212,214,0)),
  linear-gradient(170deg,#9a9ea1,#6c7175 40%,#c6c9cb 70%,#55595c)}
.work-copy{left:612px;top:2060px;width:478px}
.work-copy .kicker{font-size:14px;font-weight:700;line-height:26px;text-transform:uppercase;margin-top:28px}
.work-copy .body{font-size:14.5px;line-height:26px;color:var(--muted);text-align:justify;margin-top:14px}
.work-copy .rule{height:1px;background:#e3e3e3;margin-top:26px}
.pillars{display:flex;margin-top:20px}
.pillar{display:flex;align-items:center;gap:12px;width:166px;color:var(--navy);font-size:14px;font-weight:700;line-height:18px;text-transform:uppercase;border-right:1px solid #ddd}
.pillar + .pillar{padding-left:24px}
.pillar:last-child{border-right:0}

/* values */
.values{left:0;top:2608px;width:1200px;height:262px;display:flex;gap:3px}
.value{flex:1;background:var(--soft);text-align:center;padding-top:40px}
.value h5{color:var(--navy);font-size:14px;font-weight:700;text-transform:uppercase;margin-top:16px}
.value .bar{width:32px;height:2px;background:var(--navy);margin:10px auto 14px}
.value p{font-size:14px;line-height:25px;color:var(--muted);padding:0 18px}

/* portfolio */
.tile{width:316px;height:268px;border:3px solid var(--white);box-shadow:0 0 0 1px #e6e6e6}
.tile-overlay{display:flex;flex-direction:column;align-items:center;justify-content:center;color:var(--white);text-align:center}
.tile-overlay .frame{position:absolute;left:8px;top:8px;right:8px;bottom:8px;border:2px solid var(--white)}
.tile-overlay h6{font-family:"Merriweather",serif;font-size:16px;font-weight:700;text-transform:uppercase;margin:8px 0 14px}
.tile-overlay p{font-size:14px;line-height:22px;padding:0 30px}

/* footer */
.site-footer{left:0;top:3698px;width:1200px;height:248px;background:var(--footer)}
.footer-brand{left:120px;top:3805px;display:flex;align-items:center;gap:10px;font-family:"Merriweather",serif;font-size:44px;color:var(--white)}
.footer-brand .brand-dot{width:56px;height:56px;background:var(--white)}
.footer-nav{left:530px;top:3782px;display:flex;gap:12px;font-size:14.5px;font-weight:700;color:var(--white);text-transform:uppercase}
.social{left:530px;top:3830px;display:flex;gap:24px}
.social span{width:24px;height:24px;border-radius:50%;border:2px solid var(--white)}
.copyright{left:530px;top:3880px;font-size:14px;color:var(--white)}
</style>
</head>
<body>

<header class="abs site-header">
  <div class="abs brand" style="left:110px"><span class="brand-dot"></span>Brightvale</div>
  <nav class="abs main-nav" style="left:0;top:36px">
    <a class="active" style="left:410px">Home</a>
    <a style="left:497px">Our Services</a>
    <a style="left:640px">About Us</a>
    <a style="left:754px">Our People</a>
    <a style="left:885px">Compliance</a>
    <a style="left:1023px">Contact</a>
  </nav>
</header>

<section class="abs hero" role="img" aria-label="Cleaner in white coat and yellow gloves mopping a stainless steel commercial washroom, blue bucket beside her"></section>
<h1 class="abs hero-title">
  <span class="light">Your Source for</span><br>
  <span class="strong">Commercial &amp;<br>Food Service</span><br>
  <span class="light">Equipement<br>Cleaning</span>
</h1>
<a class="abs btn hero-btn">Get Started
  <svg width="13" height="13" viewBox="0 0 13 13"><circle cx="6.5" cy="6.5" r="6.5" fill="#fff"/><path d="M5 3.5l3 3-3 3" stroke="#0d3f86" stroke-width="1.8" fill="none"/></svg></a>
<div class="abs slider-arrow" style="left:26px"><svg width="16" height="16" viewBox="0 0 16 16"><path d="M11 2L5 8l6 6" stroke="#111" stroke-width="2.2" fill="none"/></svg></div>
<div class="abs slider-arrow" style="left:1128px"><svg width="16" height="16" viewBox="0 0 16 16"><path d="M5 2l6 6-6 6" stroke="#111" stroke-width="2.2" fill="none"/></svg></div>
<svg class="abs scroll-cue" width="24" height="62" viewBox="0 0 24 62"><rect x="3" y="1" width="18" height="32" rx="9" fill="none" stroke="#fff" stroke-width="2"/><line x1="12" y1="8" x2="12" y2="15" stroke="#fff" stroke-width="2"/><path d="M5 40l7 7 7-7M5 50l7 7 7-7" stroke="#fff" stroke-width="2" fill="none"/></svg>

<section class="abs feature-band"></section>
<svg class="abs" style="left:124px;top:708px" width="52" height="48" viewBox="0 0 52 48" fill="none" stroke="#fff" stroke-width="2"><circle cx="26" cy="14" r="8"/><path d="M2 30c6 0 10 8 16 10h16c6-2 10-10 16-10M10 46l8-6M42 46l-8-6"/></svg>
<div class="abs feature" style="left:202px;top:690px"><h4>24/7 Help Center</h4><div class="bar"></div><p>Lorem ipsum dolor sit amet,<br>consectetur adipiscing.</p></div>
<div class="abs feature-divider" style="left:411px"></div>
<svg class="abs" style="left:460px;top:708px" width="52" height="48" viewBox="0 0 52 48" fill="none" stroke="#fff" stroke-width="2"><circle cx="12" cy="10" r="5"/><circle cx="26" cy="10" r="5"/><circle cx="40" cy="10" r="5"/><path d="M4 34c0-9 16-9 16 0M18 34c0-9 16-9 16 0M32 34c0-9 16-9 16 0"/><circle cx="38" cy="38" r="7"/></svg>
<div class="abs feature" style="left:542px;top:690px"><h4>Professional Service</h4><div class="bar"></div><p>Lorem ipsum dolor sit amet,<br>consectetur adipiscing.</p></div>
<div class="abs feature-divider" style="left:752px"></div>
<svg class="abs" style="left:806px;top:710px" width="44" height="44" viewBox="0 0 44 44" fill="none" stroke="#fff" stroke-width="2"><path d="M6 38L30 14M30 14l4-10 6 6-10 4M38 38L14 14M14 14c-4 2-10-2-8-8l5 5 4-4-5-5c6-2 10 4 8 8"/></svg>
<div class="abs feature" style="left:879px;top:690px"><h4>Using Modern Tools</h4><div class="bar"></div><p>Lorem ipsum dolor sit amet,<br>consectetur adipiscing.</p></div>

<h2 class="abs section-title" style="left:455px;top:894px"><span class="title-dot"></span>Our <span class="accent">Services</span></h2>

<article class="abs service-card" style="left:111px;top:983px">
  <div class="service-photo" role="img" aria-label="Chefs working under stainless steel extraction hoods in a commercial kitchen" style="background:
    radial-gradient(ellipse 200px 60px at 240px 40px,rgba(230,232,234,.9),rgba(230,232,234,0)),
    radial-gradient(ellipse 60px 90px at 180px 220px,rgba(250,250,250,.85),rgba(250,250,250,0)),
    linear-gradient(180deg,#9ea3a7 0%,#5e6367 40%,#3a3e42 65%,#8c9094 100%)"></div>
  <div class="service-label"><b>Equipment Cleaning</b><span>&amp; Sanitisation</span></div>
</article>
<article class="abs service-card" style="left:608px;top:983px">
  <div class="service-photo" role="img" aria-label="Colourful children's playground structure with slides in front of an apartment block" style="background:
    radial-gradient(ellipse 140px 60px at 110px 110px,rgba(240,150,180,.8),rgba(240,150,180,0)),
    radial-gradient(ellipse 160px 60px at 360px 110px,rgba(235,140,170,.8),rgba(235,140,170,0)),
    radial-gradient(ellipse 260px 70px at 240px 200px,rgba(30,80,200,.9),rgba(30,80,200,0)),
    radial-gradient(ellipse 200px 50px at 240px 160px,rgba(220,40,50,.8),rgba(220,40,50,0)),
    linear-gradient(180deg,#c8a077 0%,#b98f66 40%,#3d6ad0 65%,#e0b24a 85%,#c9a064 100%)"></div>
  <div class="service-label"><b>High Pressure Gurney</b><span>&amp; Playground Cleaning</span></div>
</article>
<article class="abs service-card" style="left:111px;top:1378px">
  <div class="service-photo" role="img" aria-label="Clean, empty commercial kitchen with steel benches and gas burners" style="background:
    radial-gradient(ellipse 220px 70px at 260px 250px,rgba(60,64,68,.85),rgba(60,64,68,0)),
    radial-gradient(ellipse 200px 90px at 200px 80px,rgba(246,247,248,.9),rgba(246,247,248,0)),
    linear-gradient(170deg,#e3e6e8,#b8bcbf 50%,#7b8084 80%,#4f5458)"></div>
  <div class="service-label"><b>General Cleaning &amp;</b><span>Property Facilities Management</span></div>
</article>
<article class="abs service-card" style="left:608px;top:1378px">
  <div class="service-photo" role="img" aria-label="Worker using a high pressure water jet on paving beside a green hedge" style="background:
    radial-gradient(ellipse 120px 140px at 330px 230px,rgba(235,240,242,.85),rgba(235,240,242,0)),
    radial-gradient(ellipse 180px 90px at 120px 250px,rgba(225,150,90,.8),rgba(225,150,90,0)),
    radial-gradient(ellipse 220px 80px at 280px 100px,rgba(60,110,40,.9),rgba(60,110,40,0)),
    linear-gradient(170deg,#2d2f2a,#4e6a30 40%,#b08a62 75%,#7a6a58)"></div>
  <div class="service-label"><b>Project &amp; Recruiting</b><span>Services</span></div>
</article>

<a class="abs btn view-more">View More
  <svg width="13" height="13" viewBox="0 0 13 13"><circle cx="6.5" cy="6.5" r="6.5" fill="#fff"/><path d="M5 3.5l3 3-3 3" stroke="#0d3f86" stroke-width="1.8" fill="none"/></svg></a>

<div class="abs water-band" role="img" aria-label="Soft water splash divider"></div>

<div class="abs work-photo-a" role="img" aria-label="Worker in gloves pressure washing beside trimmed green hedges"></div>
<div class="abs work-photo-b" role="img" aria-label="Stainless steel kitchen workstation after cleaning"></div>
<div class="abs work-copy">
  <h2 class="section-title"><span class="title-dot"></span>Working <span class="accent">With Us</span></h2>
  <p class="kicker">We are Brightvale, a leading Australian cleaning<br>services company.</p>
  <p class="body">Sed ut perspiciatis unde omnis iste natus error sit voluptatem accusantium doloremque laudantium, totam rem aperiam, eaque ipsa quae ab illo inventore veritatis et quasi architecto beatae vitae dicta sunt explicabo. Nemo enim ipsam voluptatem quia voluptas sit aspernatur aut odit aut fugit, sed quia consequuntur magni dolores eos qui ratione voluptatem sequi nesciunt. Neque porro quisquam est, qui dolorem ipsum.</p>
  <div class="rule"></div>
  <div class="pillars">
    <div class="pillar"><svg width="38" height="34" viewBox="0 0 38 34" fill="none" stroke-width="2"><circle cx="17" cy="17" r="14" stroke="#0d3f86"/><circle cx="17" cy="17" r="7" stroke="#ff5a0f"/><path d="M17 17L34 4" stroke="#0d3f86"/></svg>Our<br>Purpose</div>
    <div class="pillar"><svg width="38" height="34" viewBox="0 0 38 34" fill="none" stroke-width="2"><path d="M3 17c8-12 24-12 32 0-8 12-24 12-32 0z" stroke="#0d3f86"/><circle cx="19" cy="17" r="5" stroke="#ff5a0f"/></svg>Our<br>Vision</div>
    <div class="pillar"><svg width="38" height="34" viewBox="0 0 38 34" fill="none" stroke-width="2"><rect x="3" y="4" width="32" height="24" stroke="#0d3f86"/><path d="M8 22l7-7 5 4 9-9" stroke="#ff5a0f"/></svg>Our<br>Strategy</div>
  </div>
</div>

<section class="abs values">
  <div class="value"><svg width="48" height="52" viewBox="0 0 48 52" fill="none" stroke="#ff5a0f" stroke-width="2.2"><path d="M24 3l18 7v14c0 13-9 22-18 25C15 46 6 37 6 24V10z"/><circle cx="24" cy="25" r="10"/><path d="M19 25l4 4 7-8"/></svg><h5>Safety &amp; Environment</h5><div class="bar"></div><p>At vero eos et accusamus et iusto odio dignissimos ducimus qui blanditiis praesentium</p></div>
  <div class="value"><svg width="48" height="52" viewBox="0 0 48 52" fill="none" stroke="#ff5a0f" stroke-width="2.2"><circle cx="24" cy="12" r="7"/><path d="M10 48V36c0-8 28-8 28 0v12M24 26v10M14 30l-8 8M34 30l8 8"/></svg><h5>Professionalism</h5><div class="bar"></div><p>At vero eos et accusamus et iusto odio dignissimos ducimus qui blanditiis praesentium</p></div>
  <div class="value"><svg width="52" height="52" viewBox="0 0 52 52" fill="none" stroke="#ff5a0f" stroke-width="2.2"><circle cx="26" cy="20" r="14"/><path d="M12 20h28M26 6c-6 8-6 20 0 28M26 6c6 8 6 20 0 28M4 34c6 0 12 12 22 12s16-12 22-12"/></svg><h5>Sustainability</h5><div class="bar"></div><p>At vero eos et accusamus et iusto odio dignissimos ducimus qui blanditiis praesentium</p></div>
  <div class="value"><svg width="56" height="52" viewBox="0 0 56 52" fill="none" stroke="#ff5a0f" stroke-width="2.2"><circle cx="28" cy="16" r="10"/><path d="M4 30l12-6 12 8 12-8 12 6M16 24l-4 16 10 6M40 24l4 16-10 6"/></svg><h5>Positive Working</h5><div class="bar"></div><p>At vero eos et accusamus et iusto odio dignissimos ducimus qui blanditiis praesentium</p></div>
  <div class="value"><svg width="52" height="52" viewBox="0 0 52 52" fill="none" stroke="#ff5a0f" stroke-width="2.2"><circle cx="26" cy="22" r="10"/><path d="M26 2v6M26 36v6M6 22h6M40 22h6M10 48c2-8 30-8 32 0M22 20l3 4 5-6"/></svg><h5>Respect</h5><div class="bar"></div><p>At vero eos et accusamus et iusto odio dignissimos ducimus qui blanditiis praesentium</p></div>
</section>

<h2 class="abs section-title" style="left:438px;top:2950px"><span class="title-dot"></span>Our <span class="accent">Portfolio</span></h2>

<div class="abs tile" style="left:112px;top:3053px;background:
  radial-gradient(ellipse 110px 40px at 160px 215px,rgba(200,204,206,.9),rgba(200,204,206,0)),
  radial-gradient(ellipse 40px 20px at 215px 60px,rgba(230,90,70,.8),rgba(230,90,70,0)),
  linear-gradient(90deg,#d8b77a 0%,#3b3b3b 15%,#55585a 50%,#2a2a2a 85%,#d8b77a 100%)" role="img" aria-label="Soft serve machine drip tray after cleaning"></div>
<div class="abs tile" style="left:442px;top:3053px;background:
  radial-gradient(ellipse 130px 80px at 160px 150px,rgba(210,212,213,.9),rgba(210,212,213,0)),
  linear-gradient(160deg,#c9b489,#8f9294 40%,#b5b8ba 65%,#6f7274)" role="img" aria-label="Stainless steel sink basin after sanitising"></div>
<div class="abs tile" style="left:771px;top:3053px;background:
  radial-gradient(ellipse 80px 60px at 220px 210px,rgba(248,248,248,.95),rgba(248,248,248,0)),
  linear-gradient(180deg,#2a2a2a,#4a4d4f 45%,#8b8e90 70%,#1e1e1e)" role="img" aria-label="Beverage dispenser nozzles above a white bucket"></div>
<div class="abs tile" style="left:112px;top:3337px;background:radial-gradient(circle at 50% 50%,#5a4a40 0%,#8a7468 25%,#c9bdb5 50%,#efecea 75%)" role="img" aria-label="Close-up of a mixer blade inside a steel machine"></div>
<div class="abs tile tile-overlay" style="left:442px;top:3337px;background:linear-gradient(170deg,#2f3a45,#1f2328 60%,#444)" role="img" aria-label="Stainless equipment detail with caption overlay">
  <div class="frame"></div>
  <svg width="16" height="16" viewBox="0 0 16 16" fill="none" stroke="#fff" stroke-width="2"><circle cx="6.5" cy="6.5" r="4.5"/><path d="M10 10l4 4"/></svg>
  <h6>Lorem Ipsum Dolor</h6>
  <p>Sed ut perspiciatis unde omnis iste natus error sit voluptatem accusantium doloremque laudantium, totam.</p>
</div>
<div class="abs tile" style="left:771px;top:3337px;background:
  radial-gradient(ellipse 100px 50px at 150px 110px,rgba(180,184,186,.9),rgba(180,184,186,0)),
  linear-gradient(180deg,#3a3a3a,#7c7f81 45%,#2a2a2a 75%,#181818)" role="img" aria-label="Beverage machine taps over a drip container"></div>

<footer class="abs site-footer"></footer>
<div class="abs footer-brand"><span class="brand-dot"></span>Brightvale</div>
<nav class="abs footer-nav"><span>Home</span><span>About Us</span><span>My Offers</span><span>My References</span><span>Blog</span><span>News</span></nav>
<div class="abs social" aria-label="Social links"><span></span><span></span><span></span><span></span></div>
<p class="abs copyright">© 2020 Brightvale. All Rights Reserved</p>

</body>
</html>
```